New Book Cover Design Project for book about Trade Blend

DetWe need a book cover (front, back, spine) for a new book entitled ‘Trade Blend’’ and subtitled “beyond old rules toward real buyer wishes” (inverted commas not to be part of the title and subtitle). The author is Malcolm Ferrisby. The publisher is Tessellane Insights. The finished size of the paperback version will be 5" x 8" (127 x 203.2 mm). There will be paperback, hardback, and e-book versions. The final number of pages is expected to be in the region of 80 pages. Text for the back cover is in an attached document. At the bottom of the back cover should be publisher logo (rectangular) on the left and space for the ISBN bar code on the right. The design should be original and not include any stock images that have been created by someone else or may require obtaining a copyright licence to use. Symbols in common use and not copyrighted are probably ok. There are no required images, photographs or symbols except the publisher logo at the left bottom of the back cover. Spine lettering should be UK/US style with the top of the writing nearest the front cover. The designer is free to be creative using appropriate diagrams, symbols or abstract designs. A copy of the publisher logo is attached. Designers are assured that when evaluating designs absolutely no notice whatsoever is taken of a designer's Pixel Forum ranking or status; We are completely output driven, so what matters is the design, not the ranking or status of the designer. In a similar way, designs are not evaluated as 'good' or 'bad' - the winning design will be chosen after review by a design review panel and is not decided arbitrarily by a single person. All submitted designs should be capable of effective copyright assignment. Designs submitted for consideration should include front cover, spine, and back cover.
Candidate Trade Blend words that can be included in designs, if the designer wishes, include: product, place, promotion, price, consumer, company objectives, participants, physical evidence, process of service assembly, battery life, usability, security, fashion, design, brand, appearance, health, obedience, sustainability, accessibility, value, idea, information operation, beliefs, vectors.

Target Market(s)

Academics, teachers, text book writers, and students concerned with marketing.

Industry/Entity Type

Education

Font styles to use
Serif

Requirements
Must have
• • Author on the front cover and the spine. Templates have been added to the brief for the cover with spine for a 80 page book. There are .indd and .pdf templates that can be used. the .indd and .pdf templates show where the ISBN blocks should go. The other .PDF templates have the ISBN in the wrong place (middle of the lower back cover) but have more information about the meanings of template markings. Bleeds - PLEASE NOTE - the cover printing is not exact - there is minor variation when the printers print the covers. Therefore do not have solid blocks of colour that go to the edges of the spine or spine and cover pages with different blocks of colour - solid blocks of colour may go round the spine folds a little bit! See the templates - they indicate the areas for possible printing imprecision. The ISBN numbers in the template file names are what will be used - perfect is for the paperback and case is for the hardback.
Nice to have
• • It is not necessary to have the subtitle on the spine. The final book size may not be 80 pages, therefore the spine width may change, but not by much. • Use only standard fonts.
Should not have
• • Ideally, stock images should not be used as we cannot control other uses of images created by other sources, thus potentially damaging the book branding. I don't like solid black cover or spine backgrounds.

```html
<!DOCTYPE html>
<html lang="en">
<head>
<meta charset="utf-8">
<title>Trade Blend – Book Cover</title>
<link rel="stylesheet" href="https://fonts.googleapis.com/css2?family=Crimson+Text:wght@400&family=Libre+Caslon+Text:wght@400&family=Playfair+Display:wght@400&display=swap">
<style>
  :root {
    --paper: #ffffff;
    --ink: #111111;
    --ink-soft: #6a6a6a;
    --ghost: #c4c4c4;
    --photo-tone: #8a8c8e;
    --orange: #ff7a12;
    --magenta: #c8316e;
    --plum: #7a0e6c;
    --title-plum: #8e2c5c;
    --title-rust: #c7643a;
    --publisher: #1f6f95;
  }
  * { margin: 0; padding: 0; box-sizing: border-box; }
  html, body { width: 1200px; height: 830px; overflow: hidden; background: var(--paper); }
  .cover { position: relative; width: 1200px; height: 830px; background: var(--paper); overflow: hidden; }

  /* back cover */
  .back-ghost { position: absolute; left: 0; top: 340px; width: 460px; height: 490px; }
  .back-title { position: absolute; left: 117px; top: 56px; width: 320px; text-align: center;
    font-family: "Libre Caslon Text", serif; font-weight: 400; color: var(--ink); line-height: 1; }
  .back-title .small { display: block; font-size: 31px; }
  .back-title .big { display: block; font-size: 80px; margin-top: -6px; }
  .blurb { position: absolute; left: 44px; top: 189px; width: 474px;
    font-family: "Crimson Text", serif; font-size: 14px; line-height: 16.9px;
    text-align: justify; color: var(--ink); hyphens: auto; }
  .author-photo { position: absolute; left: 46px; top: 461px; width: 183px; height: 171px;
    background: linear-gradient(160deg, #b8c2c8 0%, var(--photo-tone) 55%, #4a4d52 100%); }
  .bio { position: absolute; left: 240px; top: 511px; width: 274px;
    font-family: "Crimson Text", serif; font-size: 14.6px; line-height: 16.8px;
    text-align: justify; color: var(--ink); hyphens: auto; }
  .publisher { position: absolute; left: 48px; top: 728px; display: flex; align-items: center; gap: 6px;
    font-family: "Crimson Text", serif; font-size: 15px; color: var(--publisher); }
  .publisher .mark { width: 11px; height: 11px; background: var(--publisher); }
  .isbn-box { position: absolute; left: 346px; top: 670px; width: 165px; height: 95px;
    border: 2px solid var(--ink); background: var(--paper); }

  /* spine */
  .spine-title, .spine-author { position: absolute; transform-origin: left top; transform: rotate(90deg);
    white-space: nowrap; color: var(--ink); }
  .spine-title { left: 630px; top: 64px; font-family: "Libre Caslon Text", serif; font-size: 36px; letter-spacing: 0.02em; }
  .spine-mark { position: absolute; left: 584px; top: 413px; width: 46px; height: 34px;
    border-radius: 50%; background: var(--ink); }
  .spine-author { left: 619px; top: 484px; font-family: "Playfair Display", serif; font-size: 17px;
    letter-spacing: 0.42em; color: #333; }

  /* front cover */
  .subtitle { position: absolute; left: 696px; top: 54px; width: 470px; text-align: center;
    font-family: "Playfair Display", serif; font-size: 12.5px; letter-spacing: 0.22em;
    text-transform: uppercase; color: #555; }
  .front-art { position: absolute; left: 740px; top: 114px; width: 292px; height: 462px;
    border-radius: 36px;
    background: linear-gradient(180deg, var(--orange) 0%, var(--magenta) 48%, var(--plum) 85%); }
  .front-title { position: absolute; left: 760px; top: 598px; width: 330px; text-align: center;
    font-family: "Libre Caslon Text", serif; font-weight: 400; line-height: 1; }
  .front-title .small { display: block; font-size: 31px; color: var(--title-plum); }
  .front-title .big { display: block; font-size: 80px; margin-top: -6px;
    background: linear-gradient(90deg, var(--title-plum), var(--title-rust));
    -webkit-background-clip: text; background-clip: text; color: transparent; }
  .front-author { position: absolute; left: 680px; top: 752px; width: 500px; text-align: center;
    font-family: "Playfair Display", serif; font-size: 32px; letter-spacing: 0.3em; color: var(--ink-soft); }
</style>
</head>
<body>
<main class="cover">

  <!-- back cover -->
  <svg class="back-ghost" viewBox="0 0 460 490" aria-hidden="true">
    <path d="M0 40 C80 0 200 -10 300 30 C400 80 450 180 430 290 C415 370 380 420 360 490 L0 490 Z" fill="var(--ghost)"/>
  </svg>

  <h2 class="back-title"><span class="small">TRADE</span><span class="big">BLEND</span></h2>

  <p class="blurb">This book has been inspired by the many textbooks, classes and student work about trade blend, which simply present or teach trade blend as 4Ps - very often not even acknowledging where those 4Ps came from. This approach is simply unacceptable academic work - no discussion of the extensive research from the 1920s onwards, about what is needed for effective marketing and trade blend. In several ways, this is a thoroughly radical book pushing against the common approach of simply teaching about simplistic 4Ps. Many students produce a trade blend for a company; they shouldn't. The book provides a solid example of what academics often call 'critical thinking'. Other ways in which the book is radical, is that it shows that trade blend is not only for products and services; it is also for ideas. The book discusses the idea that marketing can be seen as a branch of information warfare. Positioning should be included in trade blend considerations. Trade blend should not only be considered for legitimate products, services, and ideas; it is relevant also for those who trade in legal or mixed legal and illegal products and services. Examples are explored in the book.</p>

  <div class="author-photo" role="img" aria-label="Author portrait photograph"></div>

  <p class="bio">Malcolm Ferrisby has extensive experience in industry, academia, and a variety of NGOs working in human and civil rights. Within those contexts, he has a lot of marketing experience as practitioner, academic, and external examiner – contributing to the radical nature of this book.</p>

  <div class="publisher"><span class="mark"></span><span>Tessellane Insights</span></div>
  <div class="isbn-box" aria-label="Space for ISBN"></div>

  <!-- spine -->
  <div class="spine-title">TRADE BLEND</div>
  <div class="spine-mark" role="img" aria-label="Small emblem"></div>
  <div class="spine-author">MALCOLM FERRISBY</div>

  <!-- front cover -->
  <p class="subtitle">beyond old rules toward real buyer wishes</p>

  <div class="front-art" role="img" aria-label="Painted light bulb illustration in orange fading to purple"></div>

  <h1 class="front-title"><span class="small">TRADE</span><span class="big">BLEND</span></h1>
  <p class="front-author">MALCOLM FERRISBY</p>

</main>
</body>
</html>
```